Redesign website for small print company

Vindurgata is a small printing company in Iceland mainly servicing Students, schools, etc. We are also doing all kind of other jobs, like business cards, book printing, brochure printing etc. We are also selling books online.
Our website is: www.vindurgata.is
What we are looking for is:
- Web Design (Uncoded - PSD layout only)
- Mobile friendly design, using our current color scheme: Red, green, yellow and light gray.
- Clean simple design
- Simple, light and easy to use.
- More menu Items/drop down
Industry/Entity Type
Digital Printing
Number of Pages Required
5+ page
Requirements
Must have
- Easy navigation
- Designed for mobile
- Current color scheme (see logo)
Nice to have
- Icon based products

```html
<!DOCTYPE html>
<html lang="en">
<head>
<meta charset="utf-8">
<title>Vindurgata – Printing for students and schools</title>
<link rel="stylesheet" href="https://fonts.googleapis.com/css2?family=Lato:ital,wght@0,400;0,700;1,400&family=Roboto:wght@500;700&display=swap">
<style>
:root{
  --green:#1f6b3d;
  --green-dark:#18592f;
  --red:#e3232a;
  --yellow:#f6cf0c;
  --gray-light:#f1f1f1;
  --gray:#e6e6e6;
  --text:#555;
  --dark:#222;
  --white:#fff;
}
*{margin:0;padding:0;box-sizing:border-box}
html,body{width:1200px;height:3255px;overflow:hidden}
body{position:relative;font-family:'Lato',sans-serif;color:var(--text);background:var(--white)}
.abs{position:absolute}
a{color:inherit;text-decoration:none}

/* top bar */
.topbar{left:0;top:0;width:1200px;height:39px;background:var(--yellow);color:var(--white);font-size:14px;font-weight:700}
.topbar span{position:absolute;top:11px;display:flex;align-items:center;gap:7px}
.topbar svg{width:14px;height:14px}

/* header */
.header{left:0;top:39px;width:1200px;height:100px;background:rgba(255,255,255,.95)}
.brand{left:118px;top:36px;display:flex;align-items:center;gap:10px;font-family:'Roboto',sans-serif;font-weight:700;font-size:29px;color:var(--dark);letter-spacing:.5px}
.brand i{display:block;width:22px;height:22px;background:var(--red)}
.nav{left:490px;top:44px;display:flex;gap:44px;font-size:18px;color:#444}
.nav .active{color:var(--dark)}
.cart{left:1022px;top:38px;width:40px;height:40px;border-radius:50%;background:var(--green)}
.cart svg{position:absolute;left:10px;top:10px}

/* hero + dropdown */
.hero{left:0;top:139px;width:1200px;height:620px;background:linear-gradient(180deg,#d8c5b6 0%,#e9b3b8 55%,#d6cfc6 100%)}
.dropdown{left:0;top:139px;width:1200px;height:393px;background:var(--green);color:var(--white);font-size:14.5px}
.dropdown::before{content:"";position:absolute;left:640px;top:-9px;border:9px solid transparent;border-top:0;border-bottom-color:var(--green)}
.dropdown ul{position:absolute;top:40px;list-style:none;line-height:30px;white-space:nowrap}
.wave{left:0;width:1200px}

/* about */
.about-title{left:128px;top:818px;font-family:'Roboto',sans-serif;font-weight:500;font-size:36px;color:var(--dark)}
.about-text{left:128px;top:882px;width:460px;font-size:17px;line-height:24px;color:#666}
.btn-green{left:126px;top:1089px;width:165px;height:42px;border-radius:21px;background:var(--green);color:var(--white);font-weight:700;font-size:15px;text-align:center;line-height:42px}
.about-art{left:597px;top:781px;width:478px;height:380px;background:linear-gradient(135deg,#7db6a1 0%,#5a9c86 45%,#e2b845 100%);border-radius:6px;transform:rotate(-2deg)}

/* products */
.products{left:0;top:1200px;width:1200px;height:640px;background:var(--red)}
.section-title{width:1200px;left:0;text-align:center;font-family:'Roboto',sans-serif;font-weight:500;font-size:31px}
.product{width:220px;color:var(--white)}
.product svg{display:block;height:76px}
.product h3{margin-top:18px;font-family:'Roboto',sans-serif;font-weight:500;font-size:21px;line-height:26px}
.product p{margin-top:12px;font-size:12.5px;line-height:19px}
.product .btn-outline{display:block;margin-top:16px;width:131px;height:34px;border:2px solid var(--white);border-radius:17px;text-align:center;line-height:30px;font-weight:700;font-size:12px}

/* work */
.work{left:0;top:1834px;width:1200px;height:446px;background:linear-gradient(180deg,#fff 0%,#ececec 100%)}
.work-item{width:260px;height:260px;border-radius:50%;border:3px solid #9a9a9a;top:1923px}
.arrow{width:30px;height:60px}

/* testimonials */
.card{width:282px;height:178px;top:2430px;background:var(--white);border-radius:4px;box-shadow:0 2px 14px rgba(0,0,0,.14);padding:28px 22px 0 56px;font-style:italic;font-size:13.5px;line-height:24px;color:#777}
.card .quote{position:absolute;left:22px;top:20px;font-family:'Roboto',sans-serif;font-style:normal;font-weight:700;font-size:44px;color:var(--yellow);line-height:1}
.author{display:flex;align-items:center;gap:14px;top:2622px}
.avatar{width:46px;height:46px;border-radius:50%;background:linear-gradient(135deg,#c9a98d,#7f6a5a)}
.author b{display:block;font-size:14px;color:var(--dark)}
.author small{font-size:12px;color:#888}

/* footer */
.footer{left:0;top:2860px;width:1200px;height:330px;background:var(--gray-light)}
.fcol h4{font-family:'Roboto',sans-serif;font-weight:500;font-size:19px;color:var(--dark);margin-bottom:14px}
.fcol ul{list-style:none;font-size:15px;line-height:31px;color:#444}
.social{display:flex;gap:6px;margin-top:10px}
.social i{display:block;width:30px;height:30px;border-radius:50%;background:#2d5da8}
.map{left:749px;top:2912px;width:332px;height:208px;background:linear-gradient(135deg,#d9d9d9,#c7c7c7)}
.copyright{left:0;top:3190px;width:1200px;height:65px;background:var(--gray);text-align:center;line-height:65px;font-size:14px;color:#777}
</style>
</head>
<body>

<div class="abs topbar">
  <span style="left:128px"><svg viewBox="0 0 14 14"><circle cx="6" cy="6" r="4.5" fill="none" stroke="#fff" stroke-width="2"/><path d="M9.5 9.5L13 13" stroke="#fff" stroke-width="2"/></svg>Search Product</span>
  <span style="left:456px"><svg viewBox="0 0 14 14"><path d="M3 1l3 3-1.5 1.5a7 7 0 004 4L10 8l3 3-2 2C6 13 1 8 1 3z" fill="#fff"/></svg>Phone: 555 0142</span>
  <span style="left:640px"><svg viewBox="0 0 14 14"><rect x="1" y="3" width="12" height="9" fill="#fff"/><path d="M1 3l6 5 6-5" fill="none" stroke="#f6cf0c" stroke-width="1.2"/></svg>verk@vindurgata.is</span>
  <span style="left:822px"><svg viewBox="0 0 14 14"><circle cx="7" cy="7" r="5.5" fill="none" stroke="#fff" stroke-width="2"/><path d="M7 4v3.5h2.5" fill="none" stroke="#fff" stroke-width="1.6"/></svg>Mon - Fri 9-17</span>
</div>

<div class="abs hero" role="img" aria-label="Photo of a student writing in an open notebook at a desk"></div>

<div class="abs header">
  <div class="abs brand"><i></i>VINDURGATA</div>
  <nav class="abs nav">
    <a>About Us</a><a class="active">Product ⌄</a><a>Submission of Works</a><a>Contact</a>
  </nav>
  <div class="abs cart"><svg width="20" height="20" viewBox="0 0 20 20"><path d="M3 7h14l-2 9H5z" fill="#fff"/><path d="M7 7V5a3 3 0 016 0v2" fill="none" stroke="#fff" stroke-width="1.8"/></svg></div>
</div>

<div class="abs dropdown">
  <ul style="left:141px">
    <li>A3 Broken Brochures</li><li>A4 Broken Brochures</li><li>Better finance</li><li>Bookprint, pounds</li><li>Calendar 2019</li><li>Comb-bound books</li><li>textbooks</li><li>Introduction to Social Thought - 2018</li><li>Photocopying</li><li>Business cards on both sides printed</li>
  </ul>
  <ul style="left:427px">
    <li>Business cards printed on one side</li><li>Essay of the Northbay University</li><li>Essay Fjordvik University</li><li>Essay various schools</li><li>Creative Process</li><li>Scanning</li><li>Reports</li><li>Digital printing</li><li>Process Mapping and Feedback Loop Planning</li><li>The craft and structure of Scholarly Writing</li>
  </ul>
  <ul style="left:793px">
    <li>Numbers Made Simple, textbook</li><li>Numbers Made Simple</li><li>Tourist brochure</li><li>Opportunity card - 10 x 15</li><li>Opportunity card 10 x 15 broken in the middle</li><li>Opportunity card 15cm x 15cm</li><li>Poster A0</li><li>Poster A1</li><li>Poster A2</li>
  </ul>
</div>

<svg class="abs wave" style="top:520px;height:250px" viewBox="0 0 1200 250" preserveAspectRatio="none">
  <path d="M760 30 Q900 -10 1010 12 L1010 24 Q900 0 770 40Z" fill="#e3232a"/>
  <path d="M0 100 Q250 190 560 150 Q900 90 1200 140 L1200 200 Q900 150 560 200 Q250 240 0 170Z" fill="#e3232a"/>
  <path d="M0 145 Q250 225 560 188 Q900 140 1200 175 L1200 195 Q900 160 560 210 Q250 245 0 185Z" fill="#f6cf0c"/>
  <path d="M0 175 Q250 240 560 205 Q900 170 1200 192 L1200 250 L0 250Z" fill="#fff"/>
</svg>

<h1 class="abs about-title">ABOUT VINDURGATA</h1>
<p class="abs about-text">University education is a company located in the campus, which has specialized in the service of school staff, as well as providing general public printing.<br>Higher education publishes seminars and first-class textbooks for courses, prints theses for lesson, as well as working on an unprecedented number of smaller pieces for students, teachers and organizations.</p>
<a class="abs btn-green">Learn More</a>
<div class="abs about-art" role="img" aria-label="Illustrated printed brochures with a cyclist cover and a yellow business card"></div>

<div class="abs products"></div>
<svg class="abs wave" style="top:1190px;height:90px" viewBox="0 0 1200 90" preserveAspectRatio="none">
  <path d="M0 0 H1200 V10 Q900 10 640 70 Q300 40 0 20Z" fill="#fff"/>
  <path d="M640 70 Q900 15 1200 10 V28 Q900 30 700 78Z" fill="#1f6b3d"/>
  <path d="M700 78 Q900 35 1200 28 V45 Q900 50 760 84Z" fill="#f6cf0c"/>
</svg>
<h2 class="abs section-title" style="top:1326px;color:#fff">OUR PRODUCTS</h2>

<div class="abs product" style="left:113px;top:1421px">
  <svg viewBox="0 0 60 76" width="60"><rect x="6" y="4" width="46" height="66" fill="none" stroke="#fff" stroke-width="3"/><path d="M14 4v66M22 4v22l6-5 6 5V4" fill="none" stroke="#fff" stroke-width="3"/></svg>
  <h3>BOOK<br>PRINTING</h3>
  <p>Class aptent taciti sociosqu ad litora torquent per conubia nostra per inceptos hymenaeos Proin</p>
  <a class="btn-outline">Learn More</a>
</div>
<div class="abs product" style="left:369px;top:1421px">
  <svg viewBox="0 0 80 76" width="80"><path d="M4 8l24-4 24 4 24-4v64l-24 4-24-4-24 4z" fill="none" stroke="#fff" stroke-width="3"/><path d="M28 4v64M52 8v64M10 20h12M10 30h12M34 20h12M34 30h12M58 18h12M58 28h12" stroke="#fff" stroke-width="3"/></svg>
  <h3>BROCHURE<br>PRINTING</h3>
  <p>Class aptent taciti sociosqu ad litora torquent per conubia nostra per inceptos hymenaeos Proin</p>
  <a class="btn-outline">Learn More</a>
</div>
<div class="abs product" style="left:625px;top:1421px">
  <svg viewBox="0 0 80 76" width="80"><path d="M4 72h72" stroke="#fff" stroke-width="3"/><rect x="6" y="10" width="14" height="60" fill="none" stroke="#fff" stroke-width="3"/><rect x="22" y="4" width="14" height="66" fill="none" stroke="#fff" stroke-width="3"/><rect x="38" y="12" width="14" height="58" fill="none" stroke="#fff" stroke-width="3"/><rect x="54" y="6" width="20" height="64" fill="none" stroke="#fff" stroke-width="3"/><path d="M6 22h14M22 18h14M38 26h14M54 20h20" stroke="#fff" stroke-width="3"/></svg>
  <h3>SELLING<br>BOOKS</h3>
  <p>Class aptent taciti sociosqu ad litora torquent per conubia nostra per inceptos hymenaeos Proin</p>
  <a class="btn-outline">Learn More</a>
</div>
<div class="abs product" style="left:879px;top:1421px">
  <svg viewBox="0 0 70 76" width="70"><rect x="4" y="14" width="62" height="50" rx="4" fill="none" stroke="#fff" stroke-width="3"/><rect x="26" y="8" width="18" height="10" fill="none" stroke="#fff" stroke-width="3"/><circle cx="22" cy="34" r="6" fill="none" stroke="#fff" stroke-width="3"/><path d="M12 52q10-14 20 0M40 32h18M40 42h18M40 52h12" fill="none" stroke="#fff" stroke-width="3"/></svg>
  <h3>BUSINESS<br>CARDS</h3>
  <p>Class aptent taciti sociosqu ad litora torquent per conubia nostra per inceptos hymenaeos Proin</p>
  <a class="btn-outline">Learn More</a>
</div>

<div class="abs work"></div>
<svg class="abs wave" style="top:1795px;height:70px" viewBox="0 0 1200 70" preserveAspectRatio="none">
  <path d="M0 0 H1200 V10 Q700 20 500 40 Q250 40 0 20Z" fill="#e3232a"/>
  <path d="M0 20 Q250 40 500 40 Q250 55 0 40Z" fill="#f6cf0c"/>
  <path d="M0 40 Q250 55 500 40 Q250 68 0 60Z" fill="#1f6b3d"/>
</svg>
<h2 class="abs section-title" style="top:1852px;color:#e3232a">OUR WORK</h2>
<svg class="abs arrow" style="left:118px;top:2013px" viewBox="0 0 30 60"><path d="M24 4L6 30l18 26" fill="none" stroke="#666" stroke-width="3"/></svg>
<div class="abs work-item" style="left:183px;background:linear-gradient(135deg,#6e8fb3,#d9a15a)" role="img" aria-label="Photo of printed travel brochures fanned out"></div>
<div class="abs work-item" style="left:480px;background:linear-gradient(135deg,#e8e4da,#f3d97a)" role="img" aria-label="Photo of bound theses and report covers"></div>
<div class="abs work-item" style="left:779px;background:linear-gradient(135deg,#f6f6f6,#bdbdbd)" role="img" aria-label="Photo of printed letterhead and business cards"></div>
<svg class="abs arrow" style="left:1052px;top:2013px" viewBox="0 0 30 60"><path d="M6 4l18 26L6 56" fill="none" stroke="#666" stroke-width="3"/></svg>

<h2 class="abs section-title" style="top:2348px;color:#1f6b3d">TESTIMONIALS</h2>
<svg class="abs arrow" style="left:94px;top:2490px" viewBox="0 0 30 60"><path d="M22 12L8 30l14 18" fill="none" stroke="#888" stroke-width="2.5"/></svg>
<div class="abs card" style="left:156px"><span class="quote">“</span>Morbi diam mauris viverra in gravida eu mattis in ante Morbi eget arcu Morbi porta libero id ullamcorper nonummy nibh ligula pulvinar metus eget</div>
<div class="abs card" style="left:477px"><span class="quote">“</span>Morbi diam mauris viverra in gravida eu mattis in ante Morbi eget arcu Morbi porta libero id ullamcorper nonummy nibh ligula pulvinar metus eget</div>
<div class="abs card" style="left:797px"><span class="quote">“</span>Morbi diam mauris viverra in gravida eu mattis in ante Morbi eget arcu Morbi porta libero id ullamcorper nonummy nibh ligula pulvinar metus eget</div>
<svg class="abs arrow" style="left:1094px;top:2490px" viewBox="0 0 30 60"><path d="M8 12l14 18L8 48" fill="none" stroke="#888" stroke-width="2.5"/></svg>
<div class="abs author" style="left:165px"><div class="avatar" role="img" aria-label="Portrait of the reviewer"></div><div><b>By Author Name</b><small>City Location</small></div></div>
<div class="abs author" style="left:486px"><div class="avatar" role="img" aria-label="Portrait of the reviewer"></div><div><b>By Author Name</b><small>City Location</small></div></div>
<div class="abs author" style="left:806px"><div class="avatar" role="img" aria-label="Portrait of the reviewer"></div><div><b>By Author Name</b><small>City Location</small></div></div>

<div class="abs footer"></div>
<svg class="abs wave" style="top:2745px;height:125px" viewBox="0 0 1200 125" preserveAspectRatio="none">
  <path d="M0 60 Q300 20 600 60 Q900 100 1200 50 V125 H0Z" fill="#f6cf0c"/>
  <path d="M0 80 Q300 30 600 70 Q900 110 1200 70 V125 H0Z" fill="#e3232a"/>
  <path d="M0 115 Q300 70 600 100 Q900 125 1200 100 V125 H0Z" fill="#f1f1f1"/>
</svg>
<div class="abs fcol" style="left:128px;top:2922px"><h4>QUICK LINKS</h4><ul><li>Home</li><li>About Us</li><li>Products</li><li>Services</li></ul></div>
<div class="abs fcol" style="left:325px;top:2920px"><h4>RESOURCES</h4><ul><li>Testimonials</li><li>Submission of works</li><li>Blogs</li><li>Contact Us</li></ul></div>
<div class="abs fcol" style="left:525px;top:2918px"><h4>CONTACT US</h4><ul><li>verk@vindurgata.is</li><li>Phone: 555 0142</li><li>Mon - Fri: 9-17</li></ul>
  <div class="social"><i></i><i style="background:#3a9be0"></i><i style="background:#3f6fb0"></i><i style="background:#2a72b5"></i></div>
</div>
<div class="abs map" role="img" aria-label="Street map showing the shop location"></div>

<div class="abs copyright">© 2018 Company Name &nbsp;All right reserved</div>
</body>
</html>
```